Vardem Web, LLC. is the name of the company that will be an Internet startup working in E-commerce and

We are a new company and going to start the business by hiring people we need. We are on “Hiring Now…” status right now which we like to be displayed on the website homepage.
The website should allow us to start the hiring process with letting people see and apply for jobs posted on the website.

the company logo is attached.

Target Market(s)

Tech Job Seekers, Programmers, iOS and Android Developers, Software engineers, Graphic designers, QA engineers, Customer Service Reps,...

Industry/Entity Type

Internet

Number of Pages Required

5+ page

Font styles to use
Serif
Sans Serif

Colors

Designer to choose colors to be used in the design.

Requirements
Must have
• We need a system to help job seekers to upload the resume and cover letter and fill the required forms and answer some questions on a form designed to evaluate the job seekers and let them know if they fit in the position and should apply for it.
• We also want job seekers to do a Pre-Employment Tests including Aptitude, Personality, and Skills after they qualified for a job which links our website to web-based pre-employment testing services websites like (Talvexa, Plivmark, Quorvane & Associates, Dunholt Assessment, …)

```html
<!DOCTYPE html>
<html lang="en">
<head>
<meta charset="utf-8">
<title>Vardem — Hiring Now</title>
<link href="https://fonts.googleapis.com/css2?family=Roboto:wght@400;500;700&family=Open+Sans:ital,wght@0,400;0,600;0,700;1,400&display=swap" rel="stylesheet">
<style>
:root{
  --orange:#f2571a;
  --blue:#3a8fd0;
  --icon-blue:#2a7fc0;
  --ink:#222;
  --text:#666;
  --light:#f4f4f4;
  --line:#d6d6d6;
  --white:#fff;
  --star:#f5c400;
}
*{margin:0;padding:0;box-sizing:border-box}
html,body{width:1200px;height:2913px;overflow:hidden}
body{position:relative;background:var(--white);font-family:"Open Sans",sans-serif;color:var(--text)}
.abs{position:absolute}
.head{font-family:"Roboto",sans-serif;color:var(--ink);font-weight:500}

/* header */
.site-header{position:absolute;left:0;top:0;width:1200px;height:93px;background:var(--white)}
.brand{position:absolute;left:97px;top:18px;display:flex;align-items:center;gap:10px;font-family:"Open Sans",sans-serif;font-weight:700;font-size:36px;color:var(--icon-blue)}
.brand .dot{width:16px;height:16px;background:var(--orange)}
.phone{position:absolute;left:646px;top:13px;display:flex;align-items:center;gap:8px;font-family:"Roboto",sans-serif;font-weight:700;font-size:17px;color:var(--ink)}
.phone .ring{width:28px;height:28px;border:2px solid var(--orange);border-radius:50%;display:flex;align-items:center;justify-content:center}
.btn-top{position:absolute;top:11px;height:36px;display:flex;align-items:center;justify-content:center;gap:6px;font-family:"Roboto",sans-serif;font-weight:700;font-size:14px;border-radius:3px}
.btn-login{left:835px;width:88px;border:2px solid var(--orange);color:var(--orange)}
.btn-upload{left:932px;width:169px;background:var(--orange);color:var(--white)}
.nav{position:absolute;top:63px;left:0;width:1200px;font-family:"Roboto",sans-serif;font-weight:700;font-size:14px;color:var(--ink)}
.nav span{position:absolute}
.nav .active{color:var(--orange)}

/* hero */
.hero{position:absolute;left:0;top:93px;width:1200px;height:439px;background:linear-gradient(110deg,#6e4a30 0%,#3a2a22 35%,#2b2b2e 60%,#4a4a4e 100%)}
.hero-title{position:absolute;top:200px;width:1200px;text-align:center;font-family:"Roboto",sans-serif;font-weight:500;font-size:54px;color:var(--white)}
.search-frame{position:absolute;left:142px;top:287px;width:916px;height:112px;border:2px solid rgba(255,255,255,.85)}
.field{position:absolute;top:320px;height:45px;background:var(--white);display:flex;align-items:center;gap:8px;padding-left:12px;font-size:13px;color:#777}
.find{position:absolute;left:717px;top:320px;width:122px;height:45px;background:var(--orange);color:var(--white);font-family:"Roboto",sans-serif;font-weight:700;font-size:15px;display:flex;align-items:center;justify-content:center}
.or{position:absolute;left:850px;top:333px;color:var(--white);font-family:"Roboto",sans-serif;font-weight:700;font-size:15px}
.cover{position:absolute;left:880px;top:320px;width:157px;height:45px;border:2px solid var(--white);color:var(--white);font-family:"Roboto",sans-serif;font-weight:700;font-size:14px;display:flex;align-items:center;justify-content:center;gap:6px}
.dots{position:absolute;top:472px;left:567px;display:flex;gap:4px}
.dots i{width:13px;height:13px;border:2px solid var(--white);border-radius:50%}
.dots i.on{background:var(--white)}

/* welcome */
.section-title{position:absolute;width:1200px;text-align:center;font-family:"Roboto",sans-serif;font-weight:500;font-size:31px;color:var(--ink)}
.intro{position:absolute;left:250px;top:662px;width:700px;text-align:center;font-size:13.5px;line-height:26px}
.feature{position:absolute;top:740px;width:300px;text-align:center}
.feature svg{display:block;margin:0 auto;height:88px}
.feature h3{font-family:"Roboto",sans-serif;font-weight:500;font-size:20px;color:var(--ink);margin-top:34px}
.feature p{font-size:13.5px;line-height:25px;margin-top:16px;padding:0 22px}
.feature .more{display:block;margin-top:20px;color:var(--orange);font-family:"Roboto",sans-serif;font-weight:700;font-size:14px}

/* audience band */
.band{position:absolute;left:0;top:1084px;width:1200px;height:285px}
.aud{position:absolute;top:1130px;width:380px;color:var(--white)}
.aud h2{font-family:"Roboto",sans-serif;font-weight:500;font-size:30px;padding-left:0}
.aud p{font-size:13.5px;line-height:26px;margin-top:14px}
.aud .btn{display:inline-flex;align-items:center;justify-content:center;height:49px;border:2px solid var(--white);padding:0 14px;margin-top:20px;font-family:"Roboto",sans-serif;font-weight:700;font-size:15px}

/* how it works */
.how-title{position:absolute;left:97px;top:1462px;font-family:"Roboto",sans-serif;font-weight:500;font-size:31px;color:var(--ink)}
.how-copy{position:absolute;left:97px;top:1522px;width:480px;font-size:13.5px;line-height:26px}
.how-copy p+p{margin-top:24px}
.btn-outline{position:absolute;left:99px;top:1703px;width:115px;height:43px;border:2px solid #444;border-radius:3px;display:flex;align-items:center;justify-content:center;font-family:"Roboto",sans-serif;font-weight:700;font-size:14px;color:var(--orange)}
.video{position:absolute;left:618px;top:1453px;width:483px;height:309px;border:6px solid var(--white);box-shadow:0 0 0 1px #ddd;background:linear-gradient(120deg,#4d4138,#8a6d55 45%,#c9a77f 70%,#6e5644)}
.play{position:absolute;left:212px;top:122px;width:60px;height:60px;border-radius:50%;background:#1b1b1b}

/* testimonials */
.testimonials{position:absolute;left:0;top:1849px;width:1200px;height:379px;background:linear-gradient(100deg,#303030,#4a4540 55%,#3a3530)}
.testimonials .section-title{color:var(--white);top:58px}
.arrow{position:absolute;top:198px;width:36px;height:36px;border:2px solid rgba(255,255,255,.8);border-radius:50%;display:flex;align-items:center;justify-content:center}
.quote{position:absolute;top:135px;width:320px}
.avatar{position:absolute;left:0;top:0;width:75px;height:75px;border-radius:50%;border:3px solid var(--white);background:#9a9a9a}
.quote .body{position:absolute;left:92px;top:0;width:240px;color:var(--white)}
.quote .body p{font-style:italic;font-size:12px;line-height:24px}
.quote .body p b{font-family:"Roboto",sans-serif;font-size:22px;font-style:normal;margin-right:6px}
.quote .name{margin-top:10px;font-size:10.5px;font-weight:600;text-transform:uppercase}
.quote .role{font-size:10.5px;font-style:italic}
.stars{margin-top:16px;display:flex;gap:3px}

/* employers */
.logo-box{position:absolute;top:2379px;width:176px;height:83px;border:1px solid #bbb;display:flex;align-items:center;justify-content:center;font-family:"Open Sans",sans-serif;font-weight:600;font-size:24px;color:#8a8a8a}

/* footer */
.site-footer{position:absolute;left:0;top:2544px;width:1200px;height:369px;background:var(--light)}
.col{position:absolute;top:63px}
.col h4{font-family:"Roboto",sans-serif;font-weight:500;font-size:17px;color:var(--ink);margin-bottom:16px}
.col li{list-style:none;font-size:12px;line-height:25px;color:#555}
.rule{position:absolute;left:99px;top:295px;width:1002px;height:1px;background:var(--line)}
.copy{position:absolute;left:99px;top:322px;font-size:12px;color:#555}
.social{position:absolute;left:975px;top:315px;display:flex;gap:10px}
.social i{width:25px;height:25px;border:1px solid #9cb4cc;border-radius:50%}
</style>
</head>
<body>

<header class="site-header">
  <div class="brand"><span class="dot"></span>Vardem</div>
  <div class="phone">
    <span class="ring"><svg width="14" height="14" viewBox="0 0 24 24"><path fill="#f2571a" d="M6.6 10.8a15 15 0 0 0 6.6 6.6l2.2-2.2c.3-.3.7-.4 1-.2 1.1.4 2.3.6 3.6.6.6 0 1 .4 1 1V20c0 .6-.4 1-1 1A17 17 0 0 1 3 4c0-.6.4-1 1-1h3.5c.6 0 1 .4 1 1 0 1.3.2 2.5.6 3.6.1.3 0 .7-.2 1z"/></svg></span>
    1 800 555 0142
  </div>
  <div class="btn-top btn-login">
    <svg width="12" height="12" viewBox="0 0 24 24"><rect x="5" y="10" width="14" height="11" rx="1" fill="#f2571a"/><path d="M8 10V7a4 4 0 0 1 8 0v3" stroke="#f2571a" stroke-width="2.5" fill="none"/></svg>LOGIN</div>
  <div class="btn-top btn-upload">
    <svg width="13" height="13" viewBox="0 0 24 24"><path fill="#fff" d="M12 3l6 7h-4v6h-4v-6H6zM4 18h16v3H4z"/></svg>UPLOAD RESUME</div>
  <nav class="nav">
    <span class="active" style="left:414px">HOME</span>
    <span style="left:482px">BROWSE JOBS</span>
    <span style="left:606px">RESUME REVIEW</span>
    <span style="left:746px">CAREER</span>
    <span style="left:825px">RESOURCES</span>
    <span style="left:934px">BLOG</span>
    <span style="left:996px">CONTACT</span>
    <span style="left:1090px;top:1px"><svg width="15" height="15" viewBox="0 0 24 24"><circle cx="10" cy="10" r="7" stroke="#222" stroke-width="3" fill="none"/><path d="M15 15l6 6" stroke="#222" stroke-width="3"/></svg></span>
  </nav>
</header>

<section class="hero" role="img" aria-label="Photo of hands typing on a laptop showing a job search page">
</section>
<h1 class="hero-title">HIRING NOW</h1>
<div class="search-frame"></div>
<div class="field" style="left:163px;width:266px">
  <svg width="12" height="12" viewBox="0 0 24 24"><circle cx="10" cy="10" r="7" stroke="#333" stroke-width="3" fill="none"/><path d="M15 15l6 6" stroke="#333" stroke-width="3"/></svg>Keyword, Job Title or Company</div>
<div class="field" style="left:441px;width:266px">
  <svg width="11" height="13" viewBox="0 0 20 24"><path fill="#333" d="M10 0a8 8 0 0 0-8 8c0 6 8 16 8 16s8-10 8-16a8 8 0 0 0-8-8zm0 11a3 3 0 1 1 0-6 3 3 0 0 1 0 6z"/></svg>City, State or Zip</div>
<div class="find">FIND JOBS</div>
<div class="or">OR</div>
<div class="cover"><svg width="13" height="13" viewBox="0 0 24 24"><circle cx="12" cy="7" r="5" fill="#fff"/><path fill="#fff" d="M2 23c0-6 4-9 10-9s10 3 10 9z"/></svg>COVER LETTER</div>
<div class="dots"><i class="on"></i><i></i><i></i><i></i></div>

<h2 class="section-title" style="top:606px">WELCOME TO VARDEM</h2>
<p class="intro">Nam libero tempore, cum soluta nobis est eligendi optio cumque nihil impedit quo minus id quod maxime placeat facere possimus, omnis voluptas assumenda est, omnis dolor repellendus.</p>

<div class="feature" style="left:85px">
  <svg viewBox="0 0 60 88" width="60"><path d="M30 4a24 24 0 0 0-14 43c3 3 4 7 4 11h20c0-4 1-8 4-11A24 24 0 0 0 30 4z" stroke="#2a7fc0" stroke-width="5" fill="none"/><rect x="19" y="64" width="22" height="6" fill="#2a7fc0"/><rect x="22" y="74" width="16" height="6" rx="3" fill="#2a7fc0"/></svg>
  <h3>Business Skills</h3>
  <p>Nam libero tempore, cum soluta no bis est eligendi optio cumque nihil impe</p>
  <span class="more">READ MORE</span>
</div>
<div class="feature" style="left:450px">
  <svg viewBox="0 0 90 88" width="90"><path fill="#2a7fc0" d="M86 8L4 42l22 10 44-34-36 40v22l14-16 20 14z"/></svg>
  <h3>Faster and Easier</h3>
  <p>Nam libero tempore, cum soluta no bis est eligendi optio cumque nihil impe</p>
  <span class="more">READ MORE</span>
</div>
<div class="feature" style="left:815px">
  <svg viewBox="0 0 88 88" width="76"><circle cx="44" cy="44" r="36" fill="#2a7fc0"/><path fill="#fff" d="M30 18c8 2 10 8 6 12s-12 2-12 10 8 6 8 14-6 10-10 8c-6-6-8-14-6-24 2-8 8-16 14-20zM52 46c6-2 14 2 14 8s-6 12-12 12-6-8-4-12z"/></svg>
  <h3>Anytime, Anywhere</h3>
  <p>Nam libero tempore, cum soluta no bis est eligendi optio cumque nihil impe</p>
  <span class="more">READ MORE</span>
</div>

<svg class="band" viewBox="0 0 1200 285" role="img" aria-label="Photos of an employer and a group of job seekers tinted blue and orange">
  <defs>
    <linearGradient id="blueTint" x1="0" x2="1"><stop offset="0" stop-color="#5b9fd2"/><stop offset="1" stop-color="#3386c8"/></linearGradient>
    <linearGradient id="orangeTint" x1="0" x2="1"><stop offset="0" stop-color="#e8520f"/><stop offset="1" stop-color="#f06a28"/></linearGradient>
  </defs>
  <rect width="1200" height="285" fill="url(#orangeTint)"/>
  <polygon points="0,0 510,0 602,142 510,285 0,285" fill="url(#blueTint)"/>
  <polygon points="510,0 680,0 602,142 680,285 510,285 602,142" fill="#ec5f1d"/>
  <polygon points="510,0 602,142 510,285 540,285 632,142 540,0" fill="#3386c8" opacity=".0"/>
  <g fill="#fff">
    <circle cx="155" cy="1139" r="0"/>
  </g>
</svg>
<svg class="abs" style="left:118px;top:1122px" width="76" height="80" viewBox="0 0 76 80"><circle cx="38" cy="22" r="18" fill="#fff"/><path fill="#fff" d="M2 78c0-20 16-34 36-34s36 14 36 34z"/></svg>
<svg class="abs" style="left:645px;top:1122px" width="92" height="80" viewBox="0 0 92 80"><circle cx="46" cy="20" r="15" fill="#fff"/><circle cx="16" cy="28" r="11" fill="#fff"/><circle cx="76" cy="28" r="11" fill="#fff"/><path fill="#fff" d="M20 78c0-18 12-32 26-32s26 14 26 32zM0 74c0-14 7-24 16-24 5 0 9 2 12 6-6 6-9 12-10 18zM92 74c0-14-7-24-16-24-5 0-9 2-12 6 6 6 9 12 10 18z"/></svg>
<div class="aud" style="left:221px">
  <h2>EMPLOYERS</h2>
  <p>At vero eos et accusamus et iusto odio dignissimos duci mus qui blanditiis praesentium voluptatum deleniti que corrupti quos dolores et quas mol.</p>
  <span class="btn" style="width:138px">POST A JOBS</span>
</div>
<div class="aud" style="left:757px">
  <h2>JOB SEEKERS</h2>
  <p>At vero eos et accusamus et iusto odio dignissimos duci mus qui blanditiis praesentium voluptatum deleniti que corrupti quos dolores et quas mol.</p>
  <span class="btn" style="width:225px">PRE-EMPLOYMENT TESTS</span>
</div>

<h2 class="how-title">HOW IT WORKS</h2>
<div class="how-copy">
  <p>At vero eos et accusamus et iusto odio dignissimos ducimus qui blanditiipr aesentium voluptatum deleniti atque corrup.</p>
  <p>Quos dolores et quas molestias excepturi sint occaecati cupiditate non pro vident, similique sunt in culpa qui officia deserunt mollitia animi, id est lab orum et dolorum fuga.</p>
</div>
<div class="btn-outline">READ MORE</div>
<div class="video" role="img" aria-label="Video still of two colleagues shaking hands over a laptop">
  <div class="play"><svg width="60" height="60" viewBox="0 0 60 60"><path d="M24 18l18 12-18 12z" fill="#fff"/></svg></div>
</div>

<section class="testimonials" role="group" aria-label="Client testimonials">
  <h2 class="section-title">CLIENT TESTIMONIALS</h2>
  <div class="arrow" style="left:30px"><svg width="12" height="12" viewBox="0 0 12 12"><path d="M8 1L3 6l5 5" stroke="#fff" stroke-width="2" fill="none"/></svg></div>
  <div class="arrow" style="left:1134px"><svg width="12" height="12" viewBox="0 0 12 12"><path d="M4 1l5 5-5 5" stroke="#fff" stroke-width="2" fill="none"/></svg></div>

  <div class="quote" style="left:97px">
    <div class="avatar" role="img" aria-label="Portrait photo of Marla Venturi"></div>
    <div class="body">
      <p><b>“</b>At vero eos et accusamus et iustodio dignissimos ducimus qui blanditiipraesnt ium voluptatum deleniti atq.</p>
      <div class="name">Marla Venturi</div>
      <div class="role">Financial Services Professional</div>
      <div class="stars">
        <svg width="100" height="18" viewBox="0 0 100 18"><g fill="#f5c400"><path id="st" d="M9 1l2.4 5.2 5.6.6-4.2 3.8 1.2 5.6L9 13.4 4 16.2l1.2-5.6L1 6.8l5.6-.6z"/><use href="#st" x="20"/><use href="#st" x="40"/><use href="#st" x="60"/></g><use href="#st" x="80" fill="none" stroke="#f5c400" stroke-width="1.3"/></svg>
      </div>
    </div>
  </div>
  <div class="quote" style="left:447px">
    <div class="avatar" role="img" aria-label="Portrait photo of Talia R. Oskarsen"></div>
    <div class="body">
      <p><b>“</b>At vero eos et accusamus et iustodio dignissimos ducimus qui blanditiipraesnt ium voluptatum deleniti atq.</p>
      <div class="name">Talia R. Oskarsen</div>
      <div class="role">National Urban Fellow at the Harbour</div>
      <div class="stars">
        <svg width="100" height="18" viewBox="0 0 100 18"><defs><linearGradient id="half"><stop offset=".5" stop-color="#f5c400"/><stop offset=".5" stop-color="transparent"/></linearGradient></defs><g fill="#f5c400"><use href="#st"/><use href="#st" x="20"/><use href="#st" x="40"/><use href="#st" x="60"/></g><use href="#st" x="80" fill="url(#half)" stroke="#f5c400" stroke-width="1.3"/></svg>
      </div>
    </div>
  </div>
  <div class="quote" style="left:795px">
    <div class="avatar" role="img" aria-label="Portrait photo of Ruth Kelvane"></div>
    <div class="body">
      <p><b>“</b>At vero eos et accusamus et iustodio dignissimos ducimus qui blanditiipraesnt ium voluptatum deleniti atq.</p>
      <div class="name">Ruth Kelvane</div>
      <div class="role">Creative Strategist | Entrepreneur &amp; Upcoming</div>
      <div class="stars">
        <svg width="100" height="18" viewBox="0 0 100 18"><g fill="#f5c400"><use href="#st"/><use href="#st" x="20"/><use href="#st" x="40"/><use href="#st" x="60"/></g><use href="#st" x="80" fill="none" stroke="#f5c400" stroke-width="1.3"/></svg>
      </div>
    </div>
  </div>
</section>

<h2 class="section-title" style="top:2304px">FEATURED EMPLOYERS</h2>
<div class="logo-box" style="left:99px">Brisko</div>
<div class="logo-box" style="left:305px">Envoyra</div>
<div class="logo-box" style="left:512px">Quellon</div>
<div class="logo-box" style="left:719px">Upwardly</div>
<div class="logo-box" style="left:925px">Skillhaven</div>

<footer class="site-footer">
  <div class="col" style="left:99px"><h4>Popular Jobs</h4><ul>
    <li>Customer Service Jobs</li><li>Administration Jobs</li><li>Healthcare Jobs</li><li>Retail Jobs</li><li>Marketing Jobs</li><li>Hospitality Jobs</li></ul></div>
  <div class="col" style="left:305px"><h4>Jobs by Location</h4><ul>
    <li>Toronto Jobs</li><li>Calgary Jobs</li><li>Edmonton Jobs</li><li>Winnipeg Jobs</li><li>Montreal Jobs</li><li>Ottawa Jobs</li></ul></div>
  <div class="col" style="left:526px"><h4>Jobs by Company</h4><ul>
    <li>Grocerly Inc</li><li>Alpine Grill</li><li>Harlow's</li><li>Prairie Health Services</li><li>Maplemart Canada</li><li>Buildright Supply Inc</li></ul></div>
  <div class="col" style="left:771px"><h4>Jobs by Category</h4><ul>
    <li>International Jobs</li><li>Blog</li><li>Career Insights</li><li>Talent Networks</li><li>Sitemap</li><li>Accessibility</li></ul></div>
  <div class="col" style="left:1002px"><h4>Legal</h4><ul>
    <li>Security &amp; Fraud</li><li>Privacy Policy</li><li>Terms</li><li>Ad Choices</li></ul></div>
  <div class="rule"></div>
  <p class="copy">Copyrights © 2017, Vardem. All rights reserved.</p>
  <div class="social" aria-label="Social links"><i></i><i></i><i></i><i></i></div>
</footer>

</body>
</html>
```